Winery needs MailChimp newsletter

Hi
We have a small vineyard in Australia and need a newsletter designed to send out whenever we release a new vintage or there's some special news - approx 4 times per year.
We would like the design [added: including colours etc] to be consistent with our website:
www.belvoria.com.au
(let us know if you need info re colours, fonts etc)
Also see the label designs on our website under Wines / Pinot Gris and Wines / Pinot Noir, to get more of a look and feel for our brand.
We plan on using mailchimp to send the newsletter out (but let us know if you'd recommend a different approach). [added: we think we'll need the mailchimp coding/html]
We're uploading the logo, a photo of a misty morning that's been used on our marketing materials in the past, as well as a photo of the current vintage that this next newsletter will announce the release of [added: it's a photo of a wine barrel, please show the whole barrel, not just the top of the barrel]. If you see other images on the website you would like to incorporate etc, please let us know.
[added: we've also uploaded an image of the grey iron shed from the logo, to be used eg as a header/footer]
Please allow space for a short intro paragraph (approx. 25-50 words), and a second area for more detailed information (approx. 50-75 words), [added: and a third area for wrapping up/other info (approx. 25-50 words)]
Lastly, we need the newsletter to link to/incorporate a pdf order form which will also be uploaded.
Thank you for your interest in this project - please don't hesitate to let us know what questions you have, thanks!
Mara K.

```html
<!DOCTYPE html>
<html lang="en">
<head>
<meta charset="utf-8">
<title>Belvoria Newsletter – Issue 1</title>
<link href="https://fonts.googleapis.com/css2?family=Tinos:wght@400;700&display=swap" rel="stylesheet">
<style>
  :root {
    --navy: #1f3444;
    --wine: #7a2317;
    --button: #6c1c11;
    --body-text: #5e5e5e;
    --rule: #8c96a0;
    --paper: #ffffff;
    --barrel-light: #b48a5c;
    --barrel-dark: #5a3a22;
    --mist-light: #d9dcda;
    --mist-green: #7c8f5a;
  }
  * { box-sizing: border-box; margin: 0; padding: 0; }
  html, body { width: 839px; height: 1200px; overflow: hidden; background: var(--paper); }
  body { font-family: "Tinos", "Times New Roman", serif; position: relative; }

  .masthead {
    position: absolute; left: 80px; top: 0; width: 270px; height: 137px;
    background: var(--navy);
    display: flex; align-items: center; justify-content: center;
  }
  .masthead__name {
    color: #ffffff; font-size: 34px; font-weight: 400; letter-spacing: 2px;
  }
  .issue {
    position: absolute; left: 671px; top: 78px;
    color: var(--wine); font-size: 22px;
  }
  .divider {
    position: absolute; left: 80px; top: 167px; width: 668px; height: 2px;
    background: var(--rule);
  }
  .photo { position: absolute; }
  .photo--barrel {
    left: 84px; top: 192px; width: 266px; height: 403px;
    background: linear-gradient(180deg, #9b8f85 0%, var(--barrel-light) 35%, var(--barrel-dark) 100%);
  }
  .photo--mist {
    left: 361px; top: 644px; width: 403px; height: 241px;
    background: linear-gradient(180deg, var(--mist-light) 0%, #c6cbc6 55%, var(--mist-green) 100%);
  }
  .headline {
    position: absolute; left: 382px; top: 182px;
    color: var(--wine); font-size: 44px; font-weight: 400; line-height: 52px;
  }
  .copy {
    position: absolute; color: var(--body-text);
    font-size: 14.5px; line-height: 28px;
  }
  .copy--intro { left: 389px; top: 270px; width: 372px; }
  .copy--detail { left: 389px; top: 450px; width: 372px; }
  .copy--wrap { left: 82px; top: 634px; width: 214px; }
  .order-button {
    position: absolute; left: 357px; top: 976px; width: 413px; height: 67px;
    background: var(--button); color: #ffffff;
    display: flex; align-items: center; justify-content: center;
    font-size: 20px; font-weight: 700; text-decoration: none; letter-spacing: 0.3px;
  }
  .footer {
    position: absolute; left: 0; top: 1127px; width: 839px; height: 73px;
    background: var(--navy); color: #ffffff;
    display: flex; align-items: center; justify-content: center;
    font-size: 14px; gap: 12px;
  }
  .footer__sep { font-weight: 700; }
</style>
</head>
<body>
  <header>
    <div class="masthead"><span class="masthead__name">BELVORIA</span></div>
    <div class="issue">ISSUE 1</div>
    <div class="divider"></div>
  </header>

  <main>
    <div class="photo photo--barrel" role="img" aria-label="Photo of an oak wine barrel from the current vintage with a wine glass resting on top"></div>
    <h1 class="headline">TITLE</h1>
    <p class="copy copy--intro">Lorem Ipsum is simply dummy text of the printing and typesetting industry. Lorem Ipsum has been the industry's standard dummy text ever since the 1500s, when an unknown printer took a galley of type and scrambled it to make a type specimen book. It has survived not only five centuries.</p>
    <p class="copy copy--detail">Lorem Ipsum is simply dummy text of the printing and typesetting industry. Lorem Ipsum has been the industry's standard dummy text ever since the 1500s, when an unknown printer took a galley of type and scrambled it to make a type specimen book. It has survived not only five centuries.</p>

    <p class="copy copy--wrap">Lorem Ipsum is simply dummy text of the printing and typesetting industry. Lorem Ipsum has been the industry's standard dummy text ever since the 1500s, when an unknown printer took a galley of type and scrambled it to make a type specimen book. It has survived not only five centuries, but also the leap into electronic typesetting, remaining essentially unchanged. It was popularised in the 1960s with the release of Lettrano sheets containing Lorem Ipsum passages. It was popularised in the 1960s with the release of Lettrano.</p>

    <div class="photo photo--mist" role="img" aria-label="Photo of the vineyard on a misty morning with gum trees and a grey shed"></div>
    <a class="order-button" href="#order-form">CLICK HERE TO PLACE AN ORDER</a>
  </main>

  <footer class="footer">
    <span>http://belvoria.com.au</span>
    <span class="footer__sep">|</span>
    <span>0491 570 156</span>
    <span class="footer__sep">|</span>
    <span>https://social.belvoria.com.au</span>
  </footer>
</body>
</html>
```